New Business Cards for Tormin Group

We need a new Business Card to compliment our new logo. We are a vibrant design, manufacture and install business providing recreation areas, public parks and Municipal spaces. We want business cards that are classy, modern and clean.

We have recently changed our logo, and are celebrating our 40th anniversary. We want business cards with a new modern design to reflect our status.

Target Market(s)

Customers

Contact Information for Business Card

We need all the details of our 3 offices as per the business card attached. Please disregard the old logo on the business card, the other three files show our new logo.

Requirements
Must have
• All info as per attached business card but with new logo.
Nice to have

```html
<!DOCTYPE html>
<html lang="en">
<head>
<meta charset="utf-8">
<title>Tormin Group – Business Card</title>
<link rel="stylesheet" href="https://fonts.googleapis.com/css2?family=Roboto:wght@300;400;500;700&display=swap">
<style>
  :root {
    --bg: #e9e6e1;
    --card: #ffffff;
    --red: #e0303e;
    --ink: #4a4a4a;
    --ink-soft: #6b6b6b;
    --logo-ink: #4d4d4f;
  }
  * { margin: 0; padding: 0; box-sizing: border-box; }
  html, body {
    width: 1200px; height: 1023px; overflow: hidden;
    background: var(--bg);
    font-family: "Roboto", Arial, sans-serif;
  }
  .stage {
    width: 1200px; height: 1023px;
    display: flex; align-items: center; justify-content: center;
  }
  .card {
    position: relative;
    width: 1000px; height: 571px;
    background: var(--card);
    border-radius: 22px;
    box-shadow: 0 12px 40px rgba(0,0,0,0.12);
    color: var(--ink);
  }
  .brand {
    position: absolute; left: 70px; top: 100px;
    display: flex; align-items: center; gap: 22px;
  }
  .brand-mark {
    width: 120px; height: 120px; border-radius: 50%;
    background: var(--red); flex: none;
  }
  .brand-name {
    display: flex; flex-direction: column;
    font-weight: 700; font-size: 46px; letter-spacing: 1px;
    color: var(--logo-ink); text-transform: uppercase; line-height: 1.05;
  }
  .person {
    position: absolute; left: 560px; top: 70px;
  }
  .person-name {
    color: var(--red); font-size: 34px; font-weight: 400;
    text-transform: uppercase; letter-spacing: 0.5px;
  }
  .person-title {
    font-size: 22px; font-weight: 300; color: var(--ink-soft);
    margin: 4px 0 14px;
  }
  .contact-line {
    display: flex; align-items: center; gap: 12px;
    font-size: 21px; font-weight: 300; line-height: 1.5;
  }
  .contact-line svg { width: 16px; height: 16px; flex: none; }
  .contact-line .hl { color: var(--red); font-weight: 400; }
  .rule {
    position: absolute; height: 2px; background: var(--red);
  }
  .rule-left { left: 70px; top: 305px; width: 300px; }
  .rule-right { left: 560px; top: 282px; width: 380px; }
  .offices {
    position: absolute; left: 70px; right: 40px; top: 330px;
    display: grid; grid-template-columns: 310px 310px 1fr;
  }
  .office-name {
    color: var(--red); font-size: 27px; font-weight: 400; margin-bottom: 6px;
  }
  .office p {
    font-size: 19px; font-weight: 300; line-height: 1.45;
  }
  .office .gap { margin-top: 16px; }
  .office .key { color: var(--red); font-weight: 400; }
</style>
</head>
<body>
<main class="stage">
  <article class="card">
    <div class="brand">
      <span class="brand-mark" aria-hidden="true"></span>
      <span class="brand-name"><span>Tormin</span><span>Group</span></span>
    </div>

    <section class="person">
      <h1 class="person-name">Samir Haddane</h1>
      <p class="person-title">Managing Partner</p>
      <p class="contact-line">
        <svg viewBox="0 0 16 16" aria-hidden="true"><path d="M4 1l3 3-1.5 2a9 9 0 0 0 4.5 4.5L12 9l3 3-2 3C7 15 1 9 1 3z" fill="none" stroke="#e0303e" stroke-width="1.3"/></svg>
        +971 (0)50 384 7162
      </p>
      <p class="contact-line">
        <svg viewBox="0 0 16 16" aria-hidden="true"><rect x="1.5" y="3.5" width="13" height="9" fill="none" stroke="#e0303e" stroke-width="1.3"/><path d="M1.5 3.5L8 9l6.5-5.5" fill="none" stroke="#e0303e" stroke-width="1.3"/></svg>
        samir@tormingroup.com
      </p>
      <p class="contact-line">
        <svg viewBox="0 0 16 16" aria-hidden="true"><circle cx="8" cy="8" r="6.5" fill="none" stroke="#e0303e" stroke-width="1.3"/><path d="M1.5 8h13M8 1.5c-3 3.5-3 9.5 0 13M8 1.5c3 3.5 3 9.5 0 13" fill="none" stroke="#e0303e" stroke-width="1.1"/></svg>
        <span>www.<span class="hl">tormingroup</span>.com</span>
      </p>
    </section>

    <span class="rule rule-left" aria-hidden="true"></span>
    <span class="rule rule-right" aria-hidden="true"></span>

    <section class="offices">
      <div class="office">
        <h2 class="office-name">Head Office</h2>
        <p>P.O. Box:</p>
        <p>41820 Abu Dhabi, U.A.E.</p>
        <p class="gap"><span class="key">P</span> : +971 (0)2 5137204</p>
        <p><span class="key">F</span> : +971 (0)2 5137205</p>
        <p><span class="key">E</span> : sales@tormingroup.com</p>
      </div>
      <div class="office">
        <h2 class="office-name">Dubai Office</h2>
        <p>P. O. Box:</p>
        <p>275146 Dubai, U.A.E.</p>
        <p class="gap"><span class="key">P</span> : +971 (0)4 3628840</p>
        <p><span class="key">F</span> : +971 (0)4 3628841</p>
        <p><span class="key">E</span> : sales@tormingroup.com</p>
      </div>
      <div class="office">
        <h2 class="office-name">Qatar Office</h2>
        <p>P. O. Box:</p>
        <p>30927 Doha, Qatar</p>
        <p class="gap"><span class="key">P</span> : +974 44718306</p>
        <p><span class="key">F</span> : +974 44718307</p>
        <p><span class="key">E</span> : sales@tormingroup.com</p>
      </div>
    </section>
  </article>
</main>
</body>
</html>
```